Quarrybend Marble & Tile Needs a Business Card

Attached you will find your logo, my photo and design guidelines for a new business card. The final design will need two separate files to create an embossed card. The cards will be printed by www.plinkprint.com (Instructions below)
Format is the Plink SQUARE card
Quarrybend Marble And Tile is a brick and mortar, retail stone and tile shop.
One the front:
Quarrybend Marble And Tile
Dorian Fesslock
Owner
24807 Hollis Verdant Blvd
Suite P & R
Charlotte, NC 28193
Cell: 704-583-7142
Web: www.QuarrybendMarbleAndTile.com
(Make each word of the domain a different or alternating color)
On the back;
Something that shows beautiful colorful tile
Follow the design guide closely please. For more information see this page that describes creating the spot gloss file: https://www.plinkprint.com/us/business-cards/design-guidelines-spot-gloss
The logo is what we would like to have raised spot glossed.
Format is the Plink SQUARE card. See attahced guidlines.

```html
<!DOCTYPE html>
<html lang="en">
<head>
<meta charset="utf-8">
<title>Quarrybend Marble &amp; Tile — Square Business Card</title>
<link rel="stylesheet" href="https://fonts.googleapis.com/css2?family=Cinzel:wght@500&family=Poppins:wght@400&display=swap">
<style>
  :root {
    --backdrop: #b7b7b7;
    --navy: #22323b;
    --ink: #1f2d36;
    --rust: #a8401f;
    --gold: #b57a2a;
    --rule: #c8944a;
    --paper: #ffffff;
    --photo-warm: #c9bca8;
    --photo-deep: #5c544c;
  }
  html, body {
    margin: 0;
    width: 1200px;
    height: 995px;
    overflow: hidden;
    background: var(--backdrop);
  }
  .stage { position: relative; width: 1200px; height: 995px; }
  .card {
    position: absolute;
    top: 328px;
    width: 398px;
    height: 401px;
    border-radius: 24px;
    overflow: hidden;
  }
  .card--back {
    left: 188px;
    background: var(--navy);
  }
  .tile-art {
    position: absolute;
    left: 0; top: 4px;
    width: 398px; height: 393px;
    background:
      radial-gradient(circle at 50% 50%, #f2efe9 0 16%, rgba(0,0,0,0) 30%),
      radial-gradient(circle at 50% 50%, rgba(168,64,31,0.85) 0 40%, rgba(212,148,48,0.55) 55%, rgba(34,50,59,0) 72%),
      var(--navy);
  }
  .card--front {
    left: 602px;
    background: var(--paper);
    font-family: "Poppins", sans-serif;
    color: var(--ink);
  }
  .portrait {
    position: absolute;
    left: 27px; top: 38px;
    width: 129px; height: 132px;
    border-radius: 8px;
    background: linear-gradient(180deg, var(--photo-warm) 0%, #b8a690 60%, var(--photo-deep) 100%);
  }
  .brand {
    position: absolute;
    left: 166px; top: 46px;
    display: flex;
    align-items: center;
    gap: 8px;
  }
  .brand__mark {
    width: 12px; height: 12px;
    background: var(--ink);
    flex: none;
  }
  .brand__name {
    font-family: "Cinzel", serif;
    font-weight: 500;
    font-size: 15px;
    line-height: 20px;
    letter-spacing: 1.5px;
    color: var(--ink);
  }
  .person__name {
    position: absolute;
    left: 173px; top: 108px;
    margin: 0;
    font-family: "Cinzel", serif;
    font-weight: 500;
    font-size: 18px;
    letter-spacing: 0.3px;
    color: var(--ink);
  }
  .person__title {
    position: absolute;
    left: 173px; top: 134px;
    margin: 0;
    font-size: 17px;
    color: var(--gold);
  }
  .rule {
    position: absolute;
    left: 26px; width: 344px;
    height: 1px;
    background: var(--rule);
  }
  .rule--top { top: 193px; }
  .rule--bottom { top: 274px; }
  .contact, .address {
    position: absolute;
    left: 0; width: 100%;
    margin: 0;
    text-align: center;
    font-size: 16.5px;
    line-height: 21px;
  }
  .contact { top: 212px; }
  .address { top: 311px; font-size: 16px; }
  .web__domain { color: var(--rust); }
  .web__tld { color: var(--gold); }
</style>
</head>
<body>
<main class="stage">
  <section class="card card--back" aria-label="Card back">
    <div class="tile-art" role="img" aria-label="Colorful geometric tile mosaic in rust, gold, sage, slate and cream around a white flower"></div>
  </section>

  <section class="card card--front" aria-label="Card front">
    <div class="portrait" role="img" aria-label="Portrait photo of the owner"></div>
    <div class="brand">
      <span class="brand__mark"></span>
      <span class="brand__name">Quarrybend<br>Marble &amp; Tile</span>
    </div>
    <h1 class="person__name">DORIAN FESSLOCK</h1>
    <p class="person__title">Owner</p>
    <div class="rule rule--top"></div>
    <p class="contact">704-583-7142<br>www.<span class="web__domain">QuarrybendMarbleAndTile</span><span class="web__tld">.com</span></p>
    <div class="rule rule--bottom"></div>
    <p class="address">24807 Hollis Verdant Blvd, Suite P &amp; R<br>Charlotte, NC 28193</p>
  </section>
</main>
</body>
</html>
```